Webpages for Vuolahtinen Software Consulting

Needed: Webpage design.
Details:
One page site with good looking fonts and simple modern design. Logo would also be nice.
Page is for Software consulting company called: "Vuolahtinen Software Consulting". Vuolahtinen is my surname.
Pages should tell viewer that the company is reliable and its employees are hard-core professionals.
Company currently has one employee, that's me. So what I do is what this company does. I am software consultant. Basicly that means that I do Java/JavaEE/Web programming as subcontractor.
Here is more detail information about me.
SPECIALTIES
- Enterprise Application Programming and Architectures,
- Web development and
- Agile development.
I have over a decade of experience on designing and creating Java based web-services and applications to multiple interfaces. I also have plenty of experience about software architectures, design patterns and integration into third party systems. I’ve got good knowledge about agile software development and testing processes and I am experienced ScrumMaster and software project leader.
Target Market(s)
IT Businesses, Coding companies... Anyone who is buying coding as service.
Industry/Entity Type
Software
Look and feel

```html
<!DOCTYPE html>
<html lang="en">
<head>
<meta charset="utf-8">
<title>Vuolahtinen Software Consulting</title>
<link href="https://fonts.googleapis.com/css2?family=Oswald:wght@400;500;700&family=PT+Serif&family=Arimo:wght@400&display=swap" rel="stylesheet">
<style>
:root{
  --ink:#1c1c1c;
  --heading-grey:#c9c9c9;
  --rule:#dcdcdc;
  --icon-grey:#d2d2d2;
  --body-text:#222;
  --band:#e4e4e4;
  --partner:#9a9a9a;
  --footer:#2b2b2b;
  --footer-text:#cfcfcf;
  --white:#ffffff;
  --arrow:#b9b9b9;
}
*{margin:0;padding:0;box-sizing:border-box}
html,body{width:1200px;height:3112px;overflow:hidden;background:var(--white)}
.page{position:relative;width:1200px;height:3112px;font-family:"Arimo",Arial,sans-serif;color:var(--body-text)}

/* header */
.brand{position:absolute;display:flex;align-items:center;gap:12px}
.brand-mark{width:34px;height:34px;background:var(--ink)}
.brand-name{font-family:"Oswald",sans-serif;font-weight:500;font-size:17px;line-height:1.1;color:var(--ink);text-transform:uppercase;letter-spacing:.5px}
.site-header .brand{left:104px;top:108px}
.main-nav{position:absolute;top:118px;left:550px;display:flex;gap:58px}
.main-nav a{font-family:"Oswald",sans-serif;font-weight:500;font-size:15px;color:var(--ink);text-decoration:none;text-transform:uppercase}

/* section headings */
.section-title{position:absolute;left:104px;width:1000px;display:flex;align-items:center;gap:18px}
.section-title h2{font-family:"Oswald",sans-serif;font-weight:700;font-size:54px;color:var(--heading-grey);text-transform:uppercase;white-space:nowrap;letter-spacing:-.5px}
.section-title .rule{flex:1;height:2px;background:var(--rule);margin-top:10px}
.section-icon{position:absolute}

/* portfolio */
.showcase{position:absolute;left:363px;top:492px;width:553px;height:352px;
  background:linear-gradient(180deg,#1d2330 0%,#0e1118 70%,#c9c9c9 88%,#9a9a9a 100%);border-radius:10px 10px 4px 4px}
.slider-arrow{position:absolute;top:634px;width:48px;height:48px;border-radius:50%;background:var(--arrow)}
.slider-arrow svg{display:block}
.slider-prev{left:98px}
.slider-next{left:1056px}

/* about */
.about-copy{position:absolute;left:104px;top:1196px;width:996px;font-size:13px;line-height:17px}
.about-copy p{margin-bottom:26px}

/* services */
.service{position:absolute;left:104px;width:996px;padding-bottom:22px;border-bottom:1px solid #eeeeee}
.service h3{font-family:"PT Serif",serif;font-weight:400;font-size:23px;color:var(--ink);margin-bottom:18px}
.service p{font-size:13px;line-height:17px}

/* partners */
.partners{position:absolute;left:0;top:2441px;width:1200px;height:222px;background:var(--band)}
.partner{position:absolute;background:var(--partner)}

/* footer */
.site-footer{position:absolute;left:0;top:2663px;width:1200px;height:449px;background:var(--footer);color:var(--footer-text);text-align:center}
.site-footer .brand{left:50%;transform:translateX(-50%);top:52px}
.site-footer .brand-mark{background:var(--white)}
.site-footer .brand-name{color:var(--white)}
.contact{position:absolute;left:0;width:1200px;top:196px;font-size:14px;line-height:24px}
.social{position:absolute;top:278px;left:50%;transform:translateX(-50%);display:flex;gap:16px}
.social span{width:34px;height:34px;background:var(--white);border-radius:4px;display:block}
.legal{position:absolute;left:0;width:1200px;top:338px;font-size:13px;line-height:28px}
.legal a{color:var(--footer-text)}
</style>
</head>
<body>
<div class="page">

  <header class="site-header">
    <div class="brand"><span class="brand-mark"></span><span class="brand-name">Vuolahtinen<br>Software Consulting</span></div>
    <nav class="main-nav">
      <a href="#portfolio">Our Portfolio</a>
      <a href="#who">Who We Are</a>
      <a href="#services">Our Services</a>
      <a href="#contact">Contact Us</a>
    </nav>
  </header>

  <section id="portfolio">
    <div class="section-title" style="top:272px"><h2>Our Portfolio</h2><span class="rule"></span><span style="width:120px"></span></div>
    <svg class="section-icon" style="left:988px;top:270px" width="120" height="90" viewBox="0 0 120 90" aria-hidden="true">
      <path d="M4 14h40l10 10h62v62H4z" fill="var(--icon-grey)"/>
      <rect x="4" y="30" width="112" height="56" fill="#c4c4c4"/>
    </svg>
    <div class="showcase" role="img" aria-label="Laptop showing a featured website project"></div>
    <a class="slider-arrow slider-prev" href="#portfolio" aria-label="Previous project">
      <svg width="48" height="48" viewBox="0 0 48 48"><path d="M28 15l-9 9 9 9" fill="none" stroke="#fff" stroke-width="4"/></svg>
    </a>
    <a class="slider-arrow slider-next" href="#portfolio" aria-label="Next project">
      <svg width="48" height="48" viewBox="0 0 48 48"><path d="M20 15l9 9-9 9" fill="none" stroke="#fff" stroke-width="4"/></svg>
    </a>
  </section>

  <section id="who">
    <div class="section-title" style="top:1016px"><h2>Who We Are</h2><span class="rule"></span><span style="width:110px"></span></div>
    <div class="section-icon" aria-hidden="true" style="left:1000px;top:988px;font-family:'Oswald',sans-serif;font-weight:700;font-size:150px;line-height:1;color:var(--icon-grey)">?</div>
    <div class="about-copy">
      <p>Vuolahtinen Software Consulting is a focused, independent consultancy that builds dependable enterprise systems for businesses that buy software development as a service. With more than a decade of hands-on experience designing and creating web services and applications for multiple interfaces, the company delivers code that is clean, tested and ready for production from the very first iteration. Every project is handled by a seasoned professional who takes full responsibility for quality, schedule and communication, so clients always know exactly where their work stands.</p>
      <p>Deep knowledge of software architectures, design patterns and integration with third party systems means new solutions fit neatly into the environments they must live in. Whether the task is a fresh enterprise platform or an extension to a mature codebase, the approach stays pragmatic, documented and easy to maintain.</p>
      <p>Agile software development and testing processes are part of daily work. As an experienced agile coach and software project leader, Vuolahtinen helps teams plan realistic iterations, keep backlogs healthy and ship working features at a steady pace. IT businesses and coding companies can rely on a consultant who joins quickly, understands the goal and delivers results without fuss.</p>
    </div>
  </section>

  <section id="services">
    <div class="section-title" style="top:1662px"><h2>Our Services</h2><span class="rule"></span><span style="width:230px"></span></div>
    <svg class="section-icon" style="left:860px;top:1630px" width="250" height="150" viewBox="0 0 250 150" aria-hidden="true">
      <g fill="var(--icon-grey)">
        <g transform="translate(80 78)">
          <circle r="50"/>
          <g><rect x="-10" y="-66" width="20" height="24"/><rect x="-10" y="42" width="20" height="24"/><rect x="-66" y="-10" width="24" height="20"/><rect x="42" y="-10" width="24" height="20"/></g>
          <g transform="rotate(45)"><rect x="-10" y="-66" width="20" height="24"/><rect x="-10" y="42" width="20" height="24"/><rect x="-66" y="-10" width="24" height="20"/><rect x="42" y="-10" width="24" height="20"/></g>
        </g>
        <g transform="translate(190 50)">
          <circle r="32"/>
          <g><rect x="-7" y="-44" width="14" height="16"/><rect x="-7" y="28" width="14" height="16"/><rect x="-44" y="-7" width="16" height="14"/><rect x="28" y="-7" width="16" height="14"/></g>
          <g transform="rotate(45)"><rect x="-7" y="-44" width="14" height="16"/><rect x="-7" y="28" width="14" height="16"/><rect x="-44" y="-7" width="16" height="14"/><rect x="28" y="-7" width="16" height="14"/></g>
        </g>
      </g>
      <circle cx="80" cy="78" r="20" fill="#fff"/>
      <circle cx="190" cy="50" r="13" fill="#fff"/>
    </svg>

    <article class="service" style="top:1874px">
      <h3>Enterprise Application Programming and Architectures</h3>
      <p>Design and implementation of robust enterprise applications, from service layers and persistence to messaging and security. Architecture reviews, performance tuning and clear technical documentation help business systems stay reliable, scalable and ready for the next stage of growth in demanding production environments.</p>
    </article>
    <article class="service" style="top:2028px">
      <h3>Web development</h3>
      <p>Modern web services and user interfaces built on proven frameworks and open standards. Clean interfaces, responsive front ends and careful integration with third party systems make web applications fast, secure and pleasant to use for customers and staff alike.</p>
    </article>
    <article class="service" style="top:2182px">
      <h3>Agile development</h3>
      <p>Hands-on agile practice as team coach and project leader. Short iterations, automated testing and open communication keep projects transparent, reduce risk and make sure the team delivers working software that truly matches the needs of the business.</p>
    </article>
  </section>

  <section class="partners" aria-label="Partners">
    <span class="partner" style="left:92px;top:98px;width:140px;height:28px;border-radius:4px"></span>
    <span class="partner" style="left:352px;top:70px;width:86px;height:82px"></span>
    <span class="partner" style="left:597px;top:68px;width:86px;height:86px;border-radius:50%"></span>
    <span class="partner" style="left:840px;top:70px;width:80px;height:80px;border-radius:50%"></span>
    <span class="partner" style="left:1082px;top:72px;width:40px;height:78px"></span>
  </section>

  <footer class="site-footer" id="contact">
    <div class="brand"><span class="brand-mark"></span><span class="brand-name">Vuolahtinen<br>Software Consulting</span></div>
    <div class="contact">
      <p>Vuolahtinen, 48 Harbour Road, Kestonbury, KB4 7QT</p>
      <p>t: +00 555 01234 &nbsp; e: info@vuolahtinen.example</p>
    </div>
    <div class="social" aria-label="Social links"><span></span><span></span><span></span></div>
    <div class="legal">
      <p>&copy; Copyright 2011</p>
      <p><a href="#">Terms &amp; Conditions</a> | <a href="#">Privacy Policy</a></p>
    </div>
  </footer>

</div>
</body>
</html>
```